Sleek wordpress site for Bramblecrest finishing works

We are a commercial job shop that serves B2B, govt & LEO and retail clients.We need a wordpress site with 6 individual pages: homepage, coating, laser engraving, laser cutting, part marking, and contact us. I have attached an outline of the desired flow and sub headings for each page. I would like to incorporate the colors of the logo through out the site to be clean and sleek enough to appeal to B2B commercial clients yet be inviting enough for retail clients.

I would like to have easy picture functionality so photographs on each page can be updated easily.

Target Market(s)

B2B industrial & Govt and Military part marking, laser engraving and coating: machine shops, aerospace companies, tool manufactures. Retail: personalized gifts, Job Shop

Coding

Coded - Design and coding required

Font styles to use
Sans Serif
Other font styles liked:
• Open to suggestion

Colors
0255a3
3176b5
eaf1f7
cfdeed
ffffff

Requirements
Must have
• Clean easy to navigate flow, separate pages as indicated on attached outline, high class feel. Great picture functionality, professional and inviting feel,
• **update: needs to be optimized for mobile, should have a gallery function. Gallery can be an additional page or embedded
Nice to have
• Social media connectivity links,
Should not have
• crappy plugins that make back-end management difficult, no blog

```html
<!DOCTYPE html>
<html lang="en">
<head>
<meta charset="utf-8">
<title>Bramblecrest Finishing Works</title>
<link href="https://fonts.googleapis.com/css2?family=Lato:wght@400;700&family=Orbitron:wght@700;800&display=swap" rel="stylesheet">
<style>
  :root{
    --brand:#0255a3;
    --brand-mid:#3176b5;
    --brand-pale:#eaf1f7;
    --brand-soft:#cfdeed;
    --brand-deep:#053f82;
    --white:#ffffff;
    --bar:#333333;
    --text:#555555;
    --heading:#666666;
  }
  *{box-sizing:border-box;margin:0;padding:0}
  html,body{width:838px;height:1200px;overflow:hidden;background:var(--white)}
  body{font-family:"Lato",sans-serif;color:var(--text);position:relative}

  .utility-bar{position:absolute;top:0;left:0;width:838px;height:29px;background:var(--bar)}
  .utility-icons{position:absolute;right:56px;top:6px;display:flex;gap:10px;align-items:center}
  .utility-icons .divider{width:1px;height:14px;background:#777}

  .site-header{position:absolute;top:29px;left:0;width:838px;height:80px;background:var(--white)}
  .brand{position:absolute;left:54px;top:26px;display:flex;align-items:center;gap:8px}
  .brand-mark{width:22px;height:22px;border-radius:50%;background:var(--brand)}
  .brand-name{font-family:"Lato",sans-serif;font-weight:700;font-size:14px;line-height:1.1;color:var(--brand);text-transform:uppercase;letter-spacing:.3px}
  .main-nav{position:absolute;top:36px;right:56px;display:flex;gap:19px;font-size:11.5px;text-transform:uppercase;color:#555}
  .main-nav .current{color:var(--brand)}

  .hero{position:absolute;top:109px;left:0;width:838px;height:393px;overflow:hidden;
    background:radial-gradient(ellipse at 75% 40%,#6a6f74 0%,#3a3c3e 35%,#1b1c1d 70%,#0e0e0e 100%)}
  .hero-sparks{position:absolute;left:340px;top:230px;width:320px;height:180px;
    background:radial-gradient(closest-side,rgba(230,140,70,.42),rgba(230,140,70,0))}
  .hero-title{position:absolute;left:55px;top:141px;font-family:"Orbitron",sans-serif;font-weight:800;font-size:25px;line-height:41px;color:var(--white);text-transform:uppercase;text-shadow:0 2px 4px rgba(0,0,0,.5)}
  .hero-tagline{position:absolute;left:55px;top:231px;font-size:15.5px;font-weight:700;color:var(--white);display:flex;align-items:center;gap:12px;text-shadow:0 1px 3px rgba(0,0,0,.5)}
  .hero-tagline .dot{width:7px;height:7px;border-radius:50%;background:var(--white)}

  .services-title{position:absolute;top:535px;left:0;width:838px;text-align:center;font-family:"Orbitron",sans-serif;font-weight:800;font-size:26px;color:var(--brand)}
  .cross-v{position:absolute;left:418px;top:659px;width:1px;height:73px;background:#ddd}
  .cross-h{position:absolute;left:382px;top:695px;width:73px;height:1px;background:#ddd}
  .service-icon{position:absolute;width:80px;height:80px}
  .service{position:absolute}
  .service h3{font-weight:400;font-size:17px;color:var(--heading);margin-bottom:5px}
  .service p{font-size:11px;line-height:17.6px;color:var(--text)}
  .service a{color:var(--brand);font-weight:700;text-decoration:underline}
  .service.left{text-align:right;left:50px;width:236px}
  .service.right{left:550px;width:226px}

  .contact{position:absolute;top:866px;left:0;width:419px;height:291px;background:var(--brand)}
  .contact h2{position:absolute;left:54px;top:57px;font-family:"Orbitron",sans-serif;font-weight:800;font-size:26px;color:var(--white)}
  .field{position:absolute;width:152px;height:32px;background:var(--white);font-size:11.5px;color:#666;padding:0 9px;display:flex;align-items:center}
  .submit{position:absolute;left:54px;top:199px;width:109px;height:32px;background:var(--brand-deep);color:var(--white);font-weight:700;font-size:14px;display:flex;align-items:center;justify-content:center}
  .map{position:absolute;top:866px;left:419px;width:419px;height:291px;background:linear-gradient(160deg,#eef0f2,#e2e5e8)}

  .site-footer{position:absolute;top:1157px;left:0;width:838px;height:43px;background:var(--bar)}
  .copyright{position:absolute;left:56px;top:15px;font-size:11px;color:#ddd}
  .social{position:absolute;right:56px;top:6px;display:flex;gap:4px}
  .social span{width:29px;height:29px;border-radius:50%;border:1px solid #ccc}
</style>
</head>
<body>
  <div class="utility-bar">
    <div class="utility-icons">
      <svg width="15" height="15" viewBox="0 0 15 15" aria-label="Search"><circle cx="6" cy="6" r="4.8" fill="none" stroke="#fff" stroke-width="1.4"/><line x1="9.5" y1="9.5" x2="14" y2="14" stroke="#fff" stroke-width="1.6"/></svg>
      <span class="divider"></span>
      <svg width="18" height="15" viewBox="0 0 18 15" aria-label="Basket"><path d="M1 5h16l-2 9H3z" fill="#fff"/><path d="M5 5l4-4 4 4" fill="none" stroke="#fff" stroke-width="1.4"/></svg>
      <span class="divider"></span>
      <svg width="15" height="15" viewBox="0 0 15 15" aria-label="Account"><circle cx="7.5" cy="4.5" r="3.8" fill="#fff"/><path d="M0 15c0-5 3-6.5 7.5-6.5S15 10 15 15z" fill="#fff"/></svg>
    </div>
  </div>

  <header class="site-header">
    <div class="brand">
      <span class="brand-mark"></span>
      <span class="brand-name">Bramblecrest<br>Finishing Works</span>
    </div>
    <nav class="main-nav">
      <span class="current">Home</span><span>Coating</span><span>Laser Engraving</span><span>Laser Cutting</span><span>Part Making</span><span>Contact</span>
    </nav>
  </header>

  <section class="hero" role="img" aria-label="Close-up photograph of a laser cutting head throwing sparks across a metal sheet">
    <div class="hero-sparks"></div>
    <h1 class="hero-title">Bramblecrest<br>Finishing Works</h1>
    <div class="hero-tagline"><span>COATING</span><span class="dot"></span><span>PART MARKING</span><span class="dot"></span><span>ENGRAVING</span></div>
  </section>

  <h2 class="services-title">OUR SERVICES</h2>
  <div class="cross-v"></div><div class="cross-h"></div>

  <svg class="service-icon" style="left:313px;top:590px" viewBox="0 0 80 80" aria-label="Part marking">
    <circle cx="40" cy="40" r="39" fill="none" stroke="var(--brand)" stroke-width="1.5"/>
    <circle cx="40" cy="40" r="36" fill="var(--brand)"/>
    <path d="M26 56l3-10 20-20 7 7-20 20zM29 46l7 7M46 29l7 7" fill="none" stroke="#fff" stroke-width="1.6" stroke-linejoin="round"/>
  </svg>
  <svg class="service-icon" style="left:442px;top:590px" viewBox="0 0 80 80" aria-label="Laser engraving">
    <circle cx="40" cy="40" r="39" fill="none" stroke="var(--brand)" stroke-width="1.5"/>
    <circle cx="40" cy="40" r="36" fill="var(--brand)"/>
    <path d="M28 24h24v5H28zM34 29h12l-3 8h-6zM40 37v13M34 46l6 4 6-4M26 52h28M26 56h28" fill="none" stroke="#fff" stroke-width="1.6" stroke-linejoin="round"/>
  </svg>
  <svg class="service-icon" style="left:313px;top:717px" viewBox="0 0 80 80" aria-label="Coatings">
    <circle cx="40" cy="40" r="39" fill="none" stroke="var(--brand)" stroke-width="1.5"/>
    <circle cx="40" cy="40" r="36" fill="var(--brand)"/>
    <path d="M40 26l17 9-17 9-17-9zM23 40l17 9 17-9M23 45l17 9 17-9" fill="none" stroke="#fff" stroke-width="1.6" stroke-linejoin="round"/>
  </svg>
  <svg class="service-icon" style="left:442px;top:717px" viewBox="0 0 80 80" aria-label="Laser cutting">
    <circle cx="40" cy="40" r="39" fill="none" stroke="var(--brand)" stroke-width="1.5"/>
    <circle cx="40" cy="40" r="36" fill="var(--brand)"/>
    <path d="M31 23v12M36 23v12M41 23v12M46 23v12M29 35h20l-5 7h-10zM39 42v12M31 50l8 4 8-4M28 57h22" fill="none" stroke="#fff" stroke-width="1.6" stroke-linejoin="round"/>
  </svg>

  <article class="service left" style="top:591px">
    <h3>Part Marking</h3>
    <p>Capabilities - Barcodes, 2d Data Matrix, UID<br>Marking, Name plates id tags Asset locator<br>tags... <a>READ MORE</a></p>
  </article>
  <article class="service right" style="top:591px">
    <h3>Laser engraving</h3>
    <p>Capabilities Statement: With our selection of<br>CO2 and fiber lasers there are very few<br>materials and substrates...<a>READ MORE</a></p>
  </article>
  <article class="service left" style="top:714px">
    <h3>Coatings</h3>
    <p>What is duraglaze - Duraglaze is a spray on<br>ceramic based finish that can be applied to<br>metals, plastics, polymers... <a>READ MORE</a></p>
  </article>
  <article class="service right" style="top:714px">
    <h3>Laser Cutting</h3>
    <p>What is laser cutting: Laser cutting is a<br>non&#8209;contact cutting process with a kurff width<br>of 0.010"... <a>READ MORE</a></p>
  </article>

  <section class="contact">
    <h2>CONTACT US</h2>
    <div class="field" style="left:54px;top:112px">Name</div>
    <div class="field" style="left:221px;top:112px">Phone No.</div>
    <div class="field" style="left:54px;top:155px">Email</div>
    <div class="field" style="left:221px;top:155px">Subject</div>
    <div class="submit">SUBMIT</div>
  </section>
  <div class="map" role="img" aria-label="Street map showing the workshop location"></div>

  <footer class="site-footer">
    <p class="copyright">©BRAMBLECREST FINISHING WORKS. 2018 - All Rights Reserved.</p>
    <div class="social"><span aria-label="Social link"></span><span aria-label="Social link"></span><span aria-label="Social link"></span></div>
  </footer>
</body>
</html>
```